Business Card Design needed for start up company Halvora

In need of a new business card designed for a start up company based in Sydney, Halvora is a new start up innovative Company, our mission it to make property accessible for everyday Australian and to become the leading Real Estate platform in Australia. We want it to be fresh and clean.

Industry/Entity Type

Financial

Contact Information for Business Card

Section for Name
Section for Title

HALVORA - The Strength of Pooling
Mobile:
Direct:

Font styles to use
Sans Serif

Colors
33a6d7
0692cd
0255a3
ffffff

Requirements
Must have
• Logo, all business card details

```html
<!DOCTYPE html>
<html lang="en">
<head>
<meta charset="utf-8">
<title>Halvora Business Card</title>
<link href="https://fonts.googleapis.com/css2?family=Jost:wght@400;600;700&display=swap" rel="stylesheet">
<style>
  :root {
    --sky: #33a6d7;
    --azure: #0692cd;
    --royal: #0255a3;
    --navy-deep: #0f2557;
    --navy-mid: #28407a;
    --ink: #16264f;
    --white: #ffffff;
    --frost-a: #e1e2e4;
    --frost-b: #c9cacd;
    --page: #eef0f3;
    --text-soft: #d6deee;
  }
  html, body {
    margin: 0;
    padding: 0;
    width: 1200px;
    height: 970px;
    overflow: hidden;
    background: var(--page);
    font-family: "Jost", "Helvetica Neue", Arial, sans-serif;
  }
  .business-card {
    position: absolute;
    left: 100px;
    top: 200px;
    width: 1000px;
    height: 570px;
    border-radius: 22px;
    overflow: hidden;
    background: linear-gradient(160deg, var(--frost-a), var(--frost-b));
    box-shadow: 0 14px 40px rgba(20, 35, 70, 0.18);
  }
  .card-shapes {
    position: absolute;
    inset: 0;
  }
  .brand-name {
    position: absolute;
    right: 76px;
    top: 114px;
    margin: 0;
    font-weight: 700;
    font-size: 76px;
    letter-spacing: 1px;
    color: var(--ink);
    line-height: 1;
  }
  .contact-block {
    position: absolute;
    left: 56px;
    top: 236px;
    color: var(--white);
  }
  .person-name {
    margin: 0;
    font-weight: 600;
    font-size: 32px;
    letter-spacing: 1px;
    color: var(--sky);
    line-height: 1.1;
  }
  .person-title {
    margin: 4px 0 0;
    font-size: 25px;
    font-weight: 400;
    letter-spacing: 0.5px;
    line-height: 1.2;
  }
  .address {
    margin: 16px 0 0;
    font-size: 23px;
    line-height: 1.38;
    font-style: normal;
  }
  .contact-list {
    list-style: none;
    margin: 14px 0 0;
    padding: 0;
  }
  .contact-list li {
    display: flex;
    align-items: center;
    gap: 12px;
    font-size: 23px;
    line-height: 32px;
  }
  .contact-list li.online {
    color: var(--text-soft);
    font-size: 21px;
  }
  .contact-icon {
    width: 20px;
    height: 20px;
    flex: none;
    fill: var(--azure);
  }
</style>
</head>
<body>
  <section class="business-card">
    <svg class="card-shapes" width="1000" height="570" viewBox="0 0 1000 570">
      <defs>
        <linearGradient id="panelGradient" x1="0" y1="0" x2="1" y2="1">
          <stop offset="0" stop-color="#28407a"/>
          <stop offset="0.55" stop-color="#0f2557"/>
          <stop offset="1" stop-color="#0b1c46"/>
        </linearGradient>
      </defs>
      <polygon points="0,0 348,0 589,570 0,570" fill="url(#panelGradient)"/>
      <line x1="354" y1="0" x2="595" y2="570" stroke="#0692cd" stroke-width="4"/>
    </svg>

    <p class="brand-name">HALVORA</p>

    <div class="contact-block">
      <h1 class="person-name">LIAM CARTER</h1>
      <p class="person-title">CEO/FOUNDER</p>
      <address class="address">2140 Harbour Street<br>Sydney, NSW 2000</address>
      <ul class="contact-list">
        <li>
          <svg class="contact-icon" viewBox="0 0 20 20"><path d="M4 1.5l3.2 3.4-1.6 2.4c.9 2.3 2.6 4.1 4.9 5.1l2.3-1.6 3.5 3.1-2 3.1C8.4 16.9 3 11.5 1 5.4z"/></svg>
          <span>612 904 3318</span>
        </li>
        <li>
          <svg class="contact-icon" viewBox="0 0 20 20"><path d="M5 1h10v18H5zM7 3v11h6V3zM9 15.5h2v1.5H9z" fill-rule="evenodd"/></svg>
          <span>614 275 0861</span>
        </li>
        <li class="online">
          <svg class="contact-icon" viewBox="0 0 20 20"><path d="M1 4h18v12H1zM2.5 5.5L10 11l7.5-5.5"/></svg>
          <span>liam@halvora.com</span>
        </li>
        <li class="online">
          <svg class="contact-icon" viewBox="0 0 20 20"><circle cx="10" cy="10" r="9"/><path d="M1 10h18M10 1c-3 3-3 15 0 18M10 1c3 3 3 15 0 18" stroke="#0f2557" stroke-width="1.3" fill="none"/></svg>
          <span>www.halvora.com</span>
        </li>
      </ul>
    </div>
  </section>
</body>
</html>
```